Vernac Law Business cards and stationary design project

We are looking for a stationary design for business cards (double sided), 8x10, 5x7, and legal and standard envelopes.

We would like the design to match the logo that we have already.
Color palate preferred is Teal, White, grey and any others that will look good for a professional law firm.

We would like this statement: "RELATIONSHIPS. RESPECT. RESULT" to be on the back of the business cards and maybe on the stationary if it looks good.

Please see link to website for more information: www.vernac-law.example

Target Market(s)

Potential clients that need Attorney services.

Industry/Entity Type

Law Firm

Contact Information for Business Card

We would like the front and back to be two different colors. Current business cards are teal front, grey back and are a vertical design. We are open to options with colors.

Font styles to use
Serif

Colors
33a6d7
33b8a4
b9b9b9
5c5c5c

Requirements
Must have
• Logo supplied needs to go on the card and stationary.
• Match website color palate, www.vernac-law.example
• Be professional and not too wordy.
• Criminal Law, Civil Litigation, Personal Injury, Restraining Orders need to be on the card.
Nice to have
• RELATIONSHIPS. RESPECT. RESULTS. on the back of the card.
Should not have
• Not be too busy/wordy or too flashy.

```html
<!DOCTYPE html>
<html lang="en">
<head>
<meta charset="utf-8">
<title>Vernac Law — Business Card</title>
<link rel="stylesheet" href="https://fonts.googleapis.com/css2?family=Open+Sans:wght@400;600;700&display=swap">
<style>
  :root {
    --backdrop: #3b3b3d;
    --card: #18191b;
    --teal: #1d93a6;
    --white: #f2f2f2;
    --rule: #2d2f31;
  }
  * { box-sizing: border-box; margin: 0; padding: 0; }
  html, body { width: 1200px; height: 900px; overflow: hidden; }
  body {
    background: var(--backdrop);
    font-family: "Open Sans", Arial, sans-serif;
    position: relative;
  }
  .card {
    position: absolute;
    top: 305px;
    width: 500px;
    height: 290px;
    background: var(--card);
    border-radius: 22px;
  }
  .card--front { left: 70px; }
  .card--back { left: 630px; }

  /* Front */
  .front-brand {
    position: absolute;
    left: 0; top: 0;
    width: 232px; height: 220px;
    display: flex; align-items: center; justify-content: center;
  }
  .brand-name {
    color: var(--teal);
    font-weight: 600;
    font-size: 30px;
    letter-spacing: 0.5px;
  }
  .front-divider {
    position: absolute;
    left: 232px; top: 40px;
    width: 1px; height: 150px;
    background: var(--rule);
  }
  .front-details {
    position: absolute;
    left: 262px; top: 34px;
    color: var(--white);
    font-size: 13px;
    line-height: 1.25;
  }
  .person-name { color: var(--teal); font-weight: 700; font-size: 17px; }
  .person-title { margin-bottom: 18px; }
  .address { margin-bottom: 14px; }
  .contact-list { list-style: none; }
  .contact-list li { display: flex; align-items: center; gap: 10px; height: 19px; }
  .contact-list svg { width: 10px; height: 10px; fill: var(--teal); flex: none; }
  .practice-areas {
    position: absolute;
    left: 0; right: 0; bottom: 26px;
    text-align: center;
    color: var(--teal);
    font-size: 14px;
    font-weight: 600;
    line-height: 1.3;
  }

  /* Back */
  .back-brand {
    position: absolute;
    left: 0; right: 0; top: 95px;
    text-align: center;
  }
  .back-brand .brand-name { font-size: 38px; }
  .back-rule {
    position: absolute;
    top: 204px; height: 1.5px;
    background: var(--teal);
  }
  .back-rule--left { left: 0; width: 92px; }
  .back-rule--right { right: 0; width: 92px; }
  .tagline {
    position: absolute;
    left: 0; right: 0; top: 195px;
    text-align: center;
    color: var(--white);
    font-weight: 700;
    font-size: 14px;
    letter-spacing: 0.2px;
  }
</style>
</head>
<body>
  <section class="card card--front" aria-label="Business card front">
    <div class="front-brand"><span class="brand-name">Vernac Law</span></div>
    <div class="front-divider"></div>
    <div class="front-details">
      <p class="person-name">Daniel Mercer</p>
      <p class="person-title">Managing Director</p>
      <p class="address">12345, Address Goes Here<br>Country Name, 123456</p>
      <ul class="contact-list">
        <li><svg viewBox="0 0 10 10"><path d="M2 0.5 L4 2.5 L3 4 Q4.5 6 6 7 L7.5 6 L9.5 8 L8 9.5 Q3 9 0.5 2 Z"/></svg>(044)-456-7890</li>
        <li><svg viewBox="0 0 10 10"><rect x="1" y="3" width="8" height="6" rx="1"/><rect x="3" y="1" width="4" height="2"/></svg>123-456-7890</li>
        <li><svg viewBox="0 0 10 10"><path d="M0 2 H10 V8 H0 Z M0.8 2.6 L5 5.6 L9.2 2.6" stroke="#18191b" stroke-width="0.8"/></svg>info@youremail.com</li>
        <li><svg viewBox="0 0 10 10"><circle cx="5" cy="5" r="4.5"/></svg>www.website.com</li>
      </ul>
    </div>
    <p class="practice-areas">Practice areas, Criminal Law, Civil Litigation/Personal Injury<br>Restraining Orders</p>
  </section>

  <section class="card card--back" aria-label="Business card back">
    <div class="back-brand"><span class="brand-name">Vernac Law</span></div>
    <div class="back-rule back-rule--left"></div>
    <p class="tagline">RELATIONSHIPS. RESPECT. RESULT</p>
    <div class="back-rule back-rule--right"></div>
  </section>
</body>
</html>
```